CBD AgriBusiness Verdant Trophy Business Card

We are HiTec producer of medical cannabis CBD Switzerland of high quality. Our website is alpinleaf.net, we will also revisit it graphically, the winner of this contest will be the graphic designer chosen for the new design of the website. We stand out by the skill of the team, many of our engineers we win cup cannabis. I join the current map to take as an example but to revisit completely: deletion of surname and first name, modification of funds (front / back), reorganization of text info, highlighting the address of the website. three characteristics define the business card: Professional, Class, refined. The business card must be optimized for soft-touch and selective varnish printing.

Target Market(s)

Customers and Suppliers

Industry/Entity Type

Agribusiness

Contact Information for Business Card

Logo, Tél / Whatsapp, mail, url du site : alpinleaf.net

Font styles to use
Sans Serif

Requirements
Must have
• Logo of alpinleaf.net
Nice to have
• a design that stands out well on the selective varnish
Should not have
• Last name and first name

```html
<!DOCTYPE html>
<html lang="en">
<head>
<meta charset="utf-8">
<title>alpinleaf business card</title>
<link href="https://fonts.googleapis.com/css2?family=Lato:wght@400;700;900&display=swap" rel="stylesheet">
<style>
  :root {
    --backdrop: #8b8b8b;
    --card-light: #ffffff;
    --card-dark: #58595b;
    --leaf-green: #8cc63f;
    --ink: #444446;
    --rule: #9a9a9a;
  }
  * { margin: 0; padding: 0; box-sizing: border-box; }
  html, body { width: 1200px; height: 1200px; overflow: hidden; }
  body {
    position: relative;
    background: var(--backdrop);
    font-family: "Lato", sans-serif;
  }
  .card {
    position: absolute;
    top: 310px;
    height: 594px;
    box-shadow: 2px 3px 6px rgba(0,0,0,0.35);
  }
  .card--front { left: 234px; width: 364px; background: var(--card-light); }
  .card--back { left: 627px; width: 370px; background: var(--card-dark); }

  .wordmark {
    position: absolute;
    display: flex;
    align-items: center;
    gap: 12px;
    white-space: nowrap;
  }
  .wordmark__square {
    width: 34px; height: 34px;
    background: var(--leaf-green);
    flex: none;
  }
  .wordmark__name {
    font-weight: 900;
    font-size: 52px;
    color: var(--leaf-green);
    letter-spacing: 0.5px;
  }
  .card--front .wordmark {
    left: 50%; top: 198px;
    transform: translate(-50%, -50%);
  }
  .card--back .wordmark {
    left: 50%; top: 296px;
    transform: translate(-50%, -50%) rotate(-90deg);
  }
  .card--back .wordmark__name { font-size: 58px; }
  .card--back .wordmark__square { width: 40px; height: 40px; }

  .contact-icons {
    position: absolute;
    left: 44px; right: 44px; top: 400px;
    display: flex;
    align-items: center;
    gap: 10px;
  }
  .contact-icons__rule { flex: 1; height: 1px; background: var(--rule); }
  .contact-icons__set { display: flex; gap: 13px; }
  .contact-icons svg { display: block; }

  .contact-details {
    position: absolute;
    left: 0; right: 0; top: 440px;
    text-align: center;
    font-size: 26px;
    line-height: 32.5px;
    color: var(--ink);
  }
</style>
</head>
<body>
  <section class="card card--front">
    <div class="wordmark">
      <span class="wordmark__square"></span>
      <span class="wordmark__name">alpinleaf</span>
    </div>

    <div class="contact-icons">
      <span class="contact-icons__rule"></span>
      <div class="contact-icons__set">
        <svg width="24" height="24" viewBox="0 0 24 24" aria-label="phone">
          <rect width="24" height="24" fill="#8cc63f"/>
          <path d="M8 5.5l2.2 2.8-1.3 1.6c.8 1.8 2.4 3.4 4.2 4.2l1.6-1.3 2.8 2.2-1.2 2.4c-4.6-.3-9.3-5-9.5-9.6z" fill="#fff"/>
        </svg>
        <svg width="24" height="24" viewBox="0 0 24 24" aria-label="email">
          <rect width="24" height="24" fill="#8cc63f"/>
          <rect x="4.5" y="7" width="15" height="10" fill="none" stroke="#fff" stroke-width="1.5"/>
          <path d="M4.5 7l7.5 6 7.5-6" fill="none" stroke="#fff" stroke-width="1.5"/>
        </svg>
        <svg width="24" height="24" viewBox="0 0 24 24" aria-label="website">
          <rect width="24" height="24" fill="#8cc63f"/>
          <circle cx="12" cy="12" r="7" fill="none" stroke="#fff" stroke-width="1.5"/>
          <ellipse cx="12" cy="12" rx="3" ry="7" fill="none" stroke="#fff" stroke-width="1.2"/>
          <path d="M5 12h14" stroke="#fff" stroke-width="1.2"/>
        </svg>
      </div>
      <span class="contact-icons__rule"></span>
    </div>

    <div class="contact-details">
      <p>+41 79 555 01 47</p>
      <p>office@alpinleaf.net</p>
      <p>www.alpinleaf.net</p>
    </div>
  </section>

  <section class="card card--back">
    <div class="wordmark">
      <span class="wordmark__square"></span>
      <span class="wordmark__name">alpinleaf</span>
    </div>
  </section>
</body>
</html>
```